Dunmore Roofing

Want a professional looking business card

Industry/Entity Type

Business

Contact Information for Business Card

Paul Dunmore ( Owner) paul@dunmoreroofing-example.com, www.dunmoreroofing-example.com, Adress: 4172 Township road 43 Brookhaven,ON K9X4T2

```html
<!DOCTYPE html>
<html lang="en">
<head>
<meta charset="utf-8">
<title>Dunmore Roofing – Business Card</title>
<link href="https://fonts.googleapis.com/css2?family=Montserrat:ital,wght@0,400;0,600;0,700;1,400&display=swap" rel="stylesheet">
<style>
  :root {
    --stage: #1b1b1d;
    --card-white: #f7f7f8;
    --brand-blue: #1d4a8f;
    --brand-blue-deep: #213a82;
    --divider: #6f7580;
    --ink-white: #ffffff;
    --ink-soft: #dfe6f3;
  }
  * { box-sizing: border-box; margin: 0; padding: 0; }
  html, body { width: 1200px; height: 963px; overflow: hidden; }
  body {
    background: var(--stage);
    font-family: "Montserrat", sans-serif;
    position: relative;
  }
  .card {
    position: absolute;
    left: 320px;
    width: 560px;
    height: 320px;
    border-radius: 14px;
    overflow: hidden;
    box-shadow: 0 12px 30px rgba(0,0,0,.5);
  }
  .card--front { top: 141px; background: var(--brand-blue); }
  .card--back {
    top: 502px;
    background: linear-gradient(135deg, var(--brand-blue) 0%, var(--brand-blue-deep) 100%);
  }

  /* Front */
  .front__brand-panel {
    position: absolute; left: 0; top: 0; bottom: 0; width: 262px;
    background: var(--card-white);
    display: flex; align-items: center; justify-content: center;
    padding: 0 20px;
  }
  .front__divider {
    position: absolute; left: 262px; top: 0; bottom: 0; width: 3px;
    background: var(--divider);
  }
  .front__notch { position: absolute; left: 265px; top: 52px; }
  .brand-name {
    display: flex; align-items: center; gap: 8px;
    font-weight: 700; text-transform: uppercase; letter-spacing: 1px;
    white-space: nowrap;
  }
  .brand-name__mark { width: 14px; height: 14px; flex: none; }
  .front__brand-panel .brand-name { color: var(--brand-blue); font-size: 16px; }
  .front__brand-panel .brand-name__mark { background: var(--brand-blue); }

  .front__details {
    position: absolute; left: 300px; top: 46px; right: 20px;
    color: var(--ink-white);
  }
  .person__name { font-size: 18px; font-weight: 700; text-transform: uppercase; letter-spacing: .5px; }
  .person__role { font-size: 11px; font-style: italic; text-transform: uppercase; margin-top: 3px; }
  .address { margin-top: 58px; font-size: 12px; line-height: 1.5; }
  .contact-list { list-style: none; margin-top: 14px; font-size: 11.5px; line-height: 1.6; }
  .contact-list li { display: flex; align-items: center; gap: 8px; white-space: nowrap; }
  .contact-list svg { width: 11px; height: 11px; flex: none; }

  /* Back */
  .back__map {
    position: absolute; inset: 30px 40px;
    background: radial-gradient(ellipse at center, rgba(255,255,255,.07), rgba(255,255,255,0) 70%);
  }
  .back__content {
    position: absolute; inset: 0;
    display: flex; flex-direction: column; align-items: center; justify-content: center;
    gap: 26px;
  }
  .card--back .brand-name { color: var(--ink-soft); font-size: 30px; letter-spacing: 2px; }
  .card--back .brand-name__mark { width: 24px; height: 24px; background: var(--ink-soft); }
  .back__web { color: var(--ink-soft); font-size: 13px; font-style: italic; }
</style>
</head>
<body>
  <section class="card card--front" aria-label="Business card front">
    <div class="front__brand-panel">
      <div class="brand-name"><span class="brand-name__mark"></span>Dunmore Roofing</div>
    </div>
    <div class="front__divider"></div>
    <svg class="front__notch" width="12" height="16" viewBox="0 0 12 16"><path d="M0 0 L12 8 L0 16 Z" fill="#f7f7f8"/></svg>
    <div class="front__details">
      <p class="person__name">Paul Dunmore</p>
      <p class="person__role">Owner</p>
      <p class="address">4172 Township road 43<br>Brookhaven, ON K9X4T2</p>
      <ul class="contact-list">
        <li><svg viewBox="0 0 12 12"><path d="M2.5 1 L4.5 3.5 L3.5 5 Q5 7.5 7 8.5 L8.5 7.5 L11 9.5 L9.5 11 Q4 10 1 2.5 Z" fill="#fff"/></svg>(000)555-0187</li>
        <li><svg viewBox="0 0 12 12"><rect x="1" y="2.5" width="10" height="7" fill="#fff"/><path d="M1 2.5 L6 6.5 L11 2.5" stroke="#1d4a8f" stroke-width="1" fill="none"/></svg>paul@dunmoreroofing-example.com</li>
        <li><svg viewBox="0 0 12 12"><circle cx="6" cy="6" r="5" fill="none" stroke="#fff" stroke-width="1.2"/><ellipse cx="6" cy="6" rx="2.2" ry="5" fill="none" stroke="#fff"/><path d="M1 6 H11" stroke="#fff"/></svg>www.dunmoreroofing-example.com</li>
      </ul>
    </div>
  </section>

  <section class="card card--back" aria-label="Business card back">
    <div class="back__map" role="img" aria-label="Faint dotted world map texture"></div>
    <div class="back__content">
      <div class="brand-name"><span class="brand-name__mark"></span>Dunmore Roofing</div>
      <p class="back__web">www.dunmoreroofing-example.com</p>
    </div>
  </section>
</body>
</html>
```